Young, dynamic furniture company needs a new business card design

We require a new business card design for our modern furniture company which supplies furniture and appliances to the property and development market.
Oakridge Interiors has become one of the leading furniture & appliance suppliers to the property market withing London. With over 10 years experience, we have increased our business to supply not only private landlords and managing agents, but also property developers, housing associations and local councils.
We offer not only a complete range of furniture which includes beds, wardrobes, dining sets and sofas, but also a high quality, full delivery and assembly service to help you with all our furnishing needs.

Target Market(s)

Private landlords, estate agents, letting agents, property management companies

Industry/Entity Type

Business

Contact Information for Business Card

Name,
Title,
Address,
Mobile,
Telephone,
Fax, Website, email address

Font styles to use
Sans Serif

Colors
3176b5
0555a3
85abd2
cfdeed

Requirements
Must have
• All the above information for each of our staff, along with our logo

```html
<!DOCTYPE html>
<html lang="en">
<head>
<meta charset="utf-8">
<title>Oakridge Interiors — Business Card</title>
<link rel="stylesheet" href="https://fonts.googleapis.com/css2?family=Montserrat:wght@400;500;600;700&family=Open+Sans:wght@400;600&display=swap">
<style>
  :root {
    --blue-mid: #3176b5;
    --blue-deep: #0555a3;
    --blue-soft: #85abd2;
    --blue-pale: #cfdeed;
    --blue-bright: #1a8fd6;
    --navy-band: #2a56a0;
    --ink: #2b2b2b;
    --paper: #ffffff;
    --stage: #eef1f5;
  }
  * { margin: 0; padding: 0; box-sizing: border-box; }
  html, body { width: 1200px; height: 780px; overflow: hidden; }
  body {
    background: var(--stage);
    font-family: "Montserrat", Arial, sans-serif;
    position: relative;
  }

  /* Front side */
  .card-front {
    position: absolute;
    left: 110px; top: 110px;
    width: 330px; height: 560px;
    background: var(--paper);
    border-radius: 18px;
    overflow: hidden;
    box-shadow: 0 6px 20px rgba(20, 40, 80, .15);
    text-align: center;
  }
  .brand {
    margin-top: 78px;
    display: flex; align-items: center; justify-content: center; gap: 10px;
  }
  .brand-square {
    width: 22px; height: 22px;
    background: var(--blue-deep);
  }
  .brand-name {
    font-size: 23px; font-weight: 500;
    letter-spacing: 1px;
    color: var(--ink);
    text-transform: uppercase;
  }
  .tagline {
    margin-top: 6px;
    font-size: 10.5px; letter-spacing: 1.2px;
    text-transform: uppercase;
    color: #555;
  }
  .person-name {
    margin-top: 34px;
    font-size: 22px; font-weight: 700;
    letter-spacing: 1.5px;
    color: var(--blue-bright);
    text-transform: uppercase;
  }
  .person-title {
    font-size: 15px; color: var(--ink);
    margin-top: -2px;
  }
  .contacts { margin-top: 22px; list-style: none; }
  .contact-item { margin-bottom: 6px; }
  .contact-label {
    display: block;
    font-size: 10px; font-weight: 600;
    color: var(--blue-bright);
  }
  .contact-value {
    display: block;
    font-size: 17px; color: var(--ink);
    letter-spacing: .5px;
    line-height: 1.1;
  }
  .email-value { font-size: 15px; }
  .web-band {
    position: absolute; left: 0; right: 0; bottom: 0;
    height: 62px;
    background: var(--navy-band);
    border-top: 4px solid var(--blue-pale);
    display: flex; align-items: center; justify-content: center;
  }
  .web-address {
    color: var(--paper);
    font-size: 17px; letter-spacing: 1px;
  }

  /* Back side */
  .card-back {
    position: absolute;
    left: 520px; top: 225px;
    width: 580px; height: 330px;
    border-radius: 18px;
    overflow: hidden;
    background: linear-gradient(135deg, var(--blue-mid) 0%, var(--blue-bright) 45%, var(--blue-deep) 100%);
    box-shadow: 0 6px 20px rgba(20, 40, 80, .18);
    font-family: "Open Sans", Arial, sans-serif;
  }
  .back-shapes { position: absolute; inset: 0; }
  .back-title {
    position: absolute; left: 0; right: 0; top: 88px;
    text-align: center;
    color: var(--paper);
    font-size: 44px; font-weight: 400;
    letter-spacing: 2px;
    text-transform: uppercase;
  }
  .back-tagline {
    position: absolute; left: 0; right: 0; top: 150px;
    text-align: center;
    color: var(--paper);
    font-size: 22px; letter-spacing: 1.5px;
    text-transform: uppercase;
  }
  .address-band {
    position: absolute; left: 0; right: 0; bottom: 0;
    height: 52px;
    background: linear-gradient(180deg, #f3f6fa, #dfe8f1);
    display: flex; align-items: center; justify-content: center;
  }
  .address {
    font-style: normal;
    font-size: 15px;
    color: var(--blue-deep);
    letter-spacing: .4px;
  }
</style>
</head>
<body>

<section class="card-front" aria-label="Business card front">
  <div class="brand">
    <span class="brand-square"></span>
    <span class="brand-name">Oakridge Interiors</span>
  </div>
  <p class="tagline">Trade Furniture Solutions</p>

  <h1 class="person-name">Daniel Hale</h1>
  <p class="person-title">Manager</p>

  <ul class="contacts">
    <li class="contact-item"><span class="contact-label">Phone</span><span class="contact-value">123 456 7890</span></li>
    <li class="contact-item"><span class="contact-label">Fax</span><span class="contact-value">123 456 7890</span></li>
    <li class="contact-item"><span class="contact-label">Mobile</span><span class="contact-value">123 456 7890</span></li>
    <li class="contact-item"><span class="contact-label">Email</span><span class="contact-value email-value">your@yourcompany.com</span></li>
  </ul>

  <div class="web-band"><span class="web-address">www.yourcompany.com</span></div>
</section>

<section class="card-back" aria-label="Business card back">
  <svg class="back-shapes" viewBox="0 0 580 330" aria-hidden="true">
    <polygon points="0,0 240,0 0,200" fill="#ffffff" opacity=".05"/>
    <polygon points="580,40 580,280 380,280" fill="#ffffff" opacity=".06"/>
    <polygon points="180,280 330,120 420,280" fill="#000000" opacity=".04"/>
  </svg>
  <h2 class="back-title">Oakridge Interiors</h2>
  <p class="back-tagline">Trade Furniture Solutions</p>
  <div class="address-band">
    <address class="address">Your Address, 2nd Ste Millbrook, Texas 1234, USA</address>
  </div>
</section>

</body>
</html>
```